Party Favors and Decorations Business Needs A Business Card Design

We are in need of a Logo design and business card design for a new small business called Bright Lantern Designs. We create party decorations and favours for Bridal Showers, Baby Showers, Weddings Birthdays etc. This is a very personalized service based on Clients theme, colour, and style. We are looking for a high end elegant look. I have attached a file to the style I like including the type of paper.

Target Market(s)

women, young adults, expectant mothers, mothers

Industry/Entity Type

Small Business

Contact Information for Business Card

Bright Lantern Designs Essex, ON 519-847-2061 brightlanterndesigns.ca karen@brightlanterngiftbox.com find us on Chatterly

Logo Text

Bright Lantern Designs

Font styles to use
Script

Requirements
Must have
• Name, email, web address, phone number
Should not have
• cutesy graphics

```html
<!DOCTYPE html>
<html lang="en">
<head>
<meta charset="utf-8">
<title>Bright Lantern Designs – Business Card</title>
<link href="https://fonts.googleapis.com/css2?family=Tinos:wght@400&family=Dancing+Script:wght@700&family=Arimo:wght@400&display=swap" rel="stylesheet">
<style>
  :root {
    --backdrop: #d9d4cc;
    --card-dark: #0b0b0b;
    --card-light: #f7f7f7;
    --ink-light: #ffffff;
    --ink-dark: #111111;
    --ink-muted: #cfcfcf;
  }
  * { box-sizing: border-box; margin: 0; padding: 0; }
  html, body {
    width: 1200px; height: 892px; overflow: hidden;
    background: var(--backdrop);
  }
  .stage {
    width: 1200px; height: 892px;
    display: flex; align-items: center; justify-content: center; gap: 80px;
  }
  .card {
    width: 340px; height: 595px;
    position: relative;
    box-shadow: 0 10px 30px rgba(0,0,0,.25);
  }
  .card--front { background: var(--card-dark); color: var(--ink-light); }
  .card--back { background: var(--card-light); color: var(--ink-dark); }

  .brand-name {
    font-family: "Tinos", "Times New Roman", serif;
    font-weight: 400;
    font-size: 36px;
    line-height: 1.05;
    text-align: center;
  }
  .card--front .brand-name { position: absolute; top: 70px; left: 0; right: 0; }
  .card--back .brand-name {
    position: absolute; top: 50%; left: 50%;
    transform: translate(-50%, -50%);
    width: 280px;
  }

  .person {
    position: absolute; top: 228px; left: 0; right: 0; text-align: center;
  }
  .person__name {
    font-family: "Dancing Script", cursive;
    font-weight: 700; font-size: 32px;
  }
  .person__role {
    font-family: "Arimo", Arial, sans-serif;
    font-size: 13px; color: var(--ink-muted); margin-top: 2px;
  }

  .contact {
    position: absolute; left: 0; right: 0; bottom: 110px;
    font-family: "Arimo", Arial, sans-serif;
    font-size: 16px; line-height: 1.55; text-align: center;
  }
  .social {
    position: absolute; left: 0; right: 0; bottom: 48px;
    display: flex; align-items: center; justify-content: center; gap: 10px;
    font-family: "Arimo", Arial, sans-serif;
  }
  .social__mark { width: 26px; height: 26px; background: var(--ink-light); border-radius: 3px; }
  .social__text { font-size: 12px; line-height: 1.1; }
  .social__text strong { display: block; font-size: 18px; font-weight: 400; }
</style>
</head>
<body>
  <main class="stage">
    <section class="card card--front" aria-label="Business card front">
      <h1 class="brand-name">Bright Lantern<br>Designs</h1>
      <div class="person">
        <p class="person__name">Employee name</p>
        <p class="person__role">Managing Director</p>
      </div>
      <address class="contact">
        519-847-2061<br>
        www.brightlanterndesigns.ca<br>
        karen@brightlanterngiftbox.com
      </address>
      <div class="social">
        <span class="social__mark"></span>
        <span class="social__text">Find us on<strong>Chatterly</strong></span>
      </div>
    </section>

    <section class="card card--back" aria-label="Business card back">
      <p class="brand-name">Bright Lantern<br>Designs</p>
    </section>
  </main>
</body>
</html>
```